Creation of a page for funnel

Our company is specialized in insoles and well-being. Our insoles help reduce joint problems, stress or ink to promote weight loss. We need a clean and refined sales page, this one will be used on funnel click. The page should display the values of our product in first: "promote weight loss" in second: "Relieves muscle and joint pain" third: "Increases energy and stress stress". The page must be in the colors of our logo (green) if possible this color: light green: dark green 54c248. It is important to follow this model for the page with totally new and fresh desing: https: // lunar-pebble. uk / qtw-lr Additionnal details for icons Section u: 1: "A unique design based on two types of knowledge" 2: "approved by acupressure expert" "Lose weight" 2: "Increases blood flow and oxygen in your body" 3: "Relieves muscle and joint pain" 4: "Increases energy and reduces stress" Section x: 1: "for men and women" 2: "one size "3:" Adjustable by cutting "Section y: 1:" powerful magnet in tourmaline "2:" for all type of shoes "3:" Flexible and light "4:" Breathable "Section z: 1:" free shipping "2 : "Customer service" 3: "money back guarantee" 4: "safe payment"
Target Market(s)
men and women 35
Number of Pages Required
1 page
Requirements
Must have
- the 5 sections mentioned in description
Nice to have
- some GIF like the funnel

```html
<!DOCTYPE html>
<html lang="en">
<head>
<meta charset="utf-8">
<title>StrideLeaf – Insoles for Well-being</title>
<link href="https://fonts.googleapis.com/css2?family=Roboto:wght@400;500;700;900&family=Open+Sans:wght@400;600&display=swap" rel="stylesheet">
<style>
:root{
  --green:#45b01a;
  --green-dark:#2f8f0e;
  --ink:#222222;
  --text:#666666;
  --dark:#333333;
  --footer:#1e1e1e;
  --light:#f3f4f3;
  --white:#ffffff;
}
*{box-sizing:border-box;margin:0;padding:0}
html,body{width:1200px;height:5089px;overflow:hidden}
body{position:relative;background:var(--white);font-family:"Open Sans",Arial,sans-serif;color:var(--text)}
.abs{position:absolute}
h1,h2,h3,h4{font-family:"Roboto",Arial,sans-serif;color:var(--ink)}
.section-title{position:absolute;left:0;width:1200px;text-align:center;font-size:40px;font-weight:700;letter-spacing:-0.5px}
.lead{position:absolute;left:215px;width:770px;text-align:center;font-size:14px;line-height:27px;color:var(--text)}

/* header */
.site-header{position:absolute;top:0;left:0;width:1200px;height:150px;background:var(--white)}
.brand{position:absolute;left:109px;top:44px;display:flex;align-items:center;gap:12px}
.brand-mark{width:40px;height:40px;border-radius:50%;background:var(--green)}
.brand-name{font-family:"Roboto",sans-serif;font-weight:700;font-size:42px;color:var(--green);line-height:42px}
.brand-tag{position:absolute;left:163px;top:92px;font-size:16px;color:var(--ink);white-space:nowrap}
.main-nav{position:absolute;top:59px;left:599px;width:490px;height:40px}
.main-nav a{position:absolute;top:0;height:40px;display:flex;align-items:center;white-space:nowrap;font-family:"Roboto",sans-serif;font-weight:500;font-size:15px;color:var(--ink);text-decoration:none}
.nav-how{left:0}
.nav-price{left:166px}
.nav-faq{left:275px}
.btn-shop{left:332px;width:156px;background:var(--green);color:#fff!important;justify-content:center;gap:6px}

/* hero */
.hero{position:absolute;top:150px;left:0;width:1200px;height:601px;overflow:hidden}
.hero-photo{position:absolute;inset:0;background:linear-gradient(160deg,#d9d2c9 0%,#b8a99b 35%,#7c6e62 60%,#3a3430 100%)}
.hero-title{position:absolute;left:109px;top:160px;font-family:"Roboto",sans-serif;font-weight:700;font-size:52px;color:#fff;letter-spacing:1px}
.hero-text{position:absolute;left:111px;top:236px;width:440px;font-size:16px;line-height:29px;color:#fff}
.btn-contact{position:absolute;left:111px;top:313px;width:164px;height:43px;background:var(--green);color:#fff;font-family:"Roboto",sans-serif;font-weight:700;font-size:15px;display:flex;align-items:center;justify-content:center}
.slider-arrow{position:absolute;top:253px;width:32px;height:32px;border-radius:50%;background:rgba(30,30,30,.75)}
.hero-wave{position:absolute;left:0;bottom:0}

/* welcome funnel */
.funnel-bar{position:absolute;height:71px;display:flex;align-items:center;justify-content:center;white-space:nowrap;font-family:"Roboto",sans-serif;font-weight:500;font-size:17px;color:#fff;clip-path:polygon(0 0,100% 0,88% 100%,12% 100%)}
.bar-dark{background:var(--dark)}
.bar-green{background:var(--green)}
.step-number{position:absolute;left:109px;top:1148px;font-family:"Roboto",sans-serif;font-weight:700;font-size:70px;color:var(--dark);line-height:76px}
.dots{position:absolute;top:1187px;height:0;border-top:2px dotted #aaa}

/* why choose */
.why{position:absolute;top:1522px;left:0;width:1200px;height:712px;background:var(--light)}
.why-circle{position:absolute;border-radius:50%;background:#fff;box-shadow:0 6px 22px rgba(0,0,0,.12);display:flex;flex-direction:column;align-items:center;justify-content:center;text-align:center}
.why-circle h3{font-size:18px;font-weight:500;line-height:24px;margin-top:14px}
.why-main{background:var(--green);border:8px solid #fff;box-shadow:0 0 0 3px var(--green),0 8px 24px rgba(0,0,0,.12)}
.why-main h3{color:#fff;font-size:18px;margin-top:18px}
.why-main p{color:#eaf7e3;font-size:13px;line-height:26px;width:250px;margin-top:8px}

/* features */
.feature-photo{position:absolute;left:108px;top:2520px;width:416px;height:416px;border-radius:50%;background:linear-gradient(150deg,var(--green) 0%,var(--green) 45%,#c9a38c 70%,#3a4a6a 100%)}
.feature{position:absolute;left:623px;width:470px;height:100px}
.feature svg{position:absolute;left:0;top:0}
.feature h4{position:absolute;left:97px;top:0;font-size:17px;font-weight:500}
.feature p{position:absolute;left:97px;top:30px;width:375px;font-size:13px;line-height:25px}

/* benefits */
.benefits{position:absolute;top:3084px;left:0;width:1200px;height:617px;background:var(--dark)}
.benefit-card{position:absolute;top:188px;width:231px;height:261px;background:#fff;text-align:center;padding-top:32px}
.benefit-card h4{font-size:18px;font-weight:500;margin-top:14px}
.benefit-card p{font-size:13px;line-height:25px;margin:14px auto 0;width:200px}

/* products */
.product{position:absolute;top:3819px;width:300px}
.product-photo{height:184px}
.product-label{height:42px;display:flex;align-items:center;justify-content:center;font-family:"Roboto",sans-serif;font-weight:700;font-size:19px;color:#fff}

/* services */
.services{position:absolute;top:4181px;left:0;width:1200px;height:534px;background:var(--light)}
.service-title{position:absolute;top:100px;left:0;width:1200px;text-align:center;font-family:"Roboto",sans-serif;font-weight:700;font-size:46px;color:var(--ink)}
.service-card{position:absolute;top:275px;width:221px;height:150px;background:#fff;text-align:center;border:1px solid #e4e4e4}
.service-icon{position:absolute;left:78px;top:-28px;width:64px;height:64px;border-radius:50%;background:#fff;border:1px solid #e4e4e4;display:flex;align-items:center;justify-content:center}
.service-card h4{margin-top:66px;font-size:15px;font-weight:500}
.service-card p{font-size:11px;line-height:19px;width:190px;margin:10px auto 0}
.chev{position:absolute;top:340px}

/* footer */
.site-footer{position:absolute;top:4715px;left:0;width:1200px;height:374px;background:var(--footer);color:#ddd}
.footer-col{position:absolute;top:62px}
.footer-col h4{color:#fff;font-size:15px;font-weight:700;margin-bottom:24px}
.footer-col li{list-style:none;font-size:14px;line-height:24px;color:#ddd}
.footer-col li::before{content:"»";margin-right:18px;color:#ddd}
.contact-row{display:flex;gap:16px;font-size:14px;line-height:22px;margin-bottom:20px}
.social{display:flex;gap:9px}
.social span{width:35px;height:35px;border-radius:50%;border:2px solid #ddd}
.pay{display:flex;gap:8px;margin-top:14px}
.pay span{width:35px;height:27px;background:#e4e4e4;border-radius:2px}
.pay span:first-child{width:62px}
.footer-rule{position:absolute;left:109px;top:300px;width:992px;border-top:1px solid #555}
.copyright{position:absolute;top:328px;left:0;width:1200px;text-align:center;font-size:14px;color:#ddd}
.to-top{position:absolute;left:20px;top:314px;width:45px;height:45px;background:var(--green);display:flex;align-items:center;justify-content:center}
</style>
</head>
<body>

<header class="site-header">
  <div class="brand"><span class="brand-mark"></span><span class="brand-name">StrideLeaf</span></div>
  <div class="brand-tag">Marchez plus léger chaque jour</div>
  <nav class="main-nav">
    <a class="nav-how" href="#">HOW IT WORKS</a>
    <a class="nav-price" href="#">PRICING</a>
    <a class="nav-faq" href="#">FAQ</a>
    <a class="btn-shop" href="#"><svg width="14" height="13" viewBox="0 0 14 13"><path d="M0 1h3l2 7h7l2-5H4" fill="none" stroke="#fff" stroke-width="1.8"/><circle cx="6" cy="11" r="1.4" fill="#fff"/><circle cx="11" cy="11" r="1.4" fill="#fff"/></svg>SHOP NOW</a>
  </nav>
</header>

<section class="hero">
  <div class="hero-photo" role="img" aria-label="Hands fitting a green insole under a bare foot on an acupressure mat"></div>
  <h1 class="hero-title">StrideLeaf</h1>
  <p class="hero-text">Lorem ipsum dolor sit amet consectetur adipiscing elit sed do eiusmod tempor.</p>
  <a class="btn-contact">CONTACT US</a>
  <div class="slider-arrow" style="left:28px"><svg width="32" height="32"><path d="M18 10l-6 6 6 6" fill="none" stroke="#fff" stroke-width="2"/></svg></div>
  <div class="slider-arrow" style="left:1136px"><svg width="32" height="32"><path d="M14 10l6 6-6 6" fill="none" stroke="#fff" stroke-width="2"/></svg></div>
  <svg class="hero-wave" width="1200" height="110" viewBox="0 0 1200 110">
    <path d="M0 52 C250 20 450 90 720 72 C900 60 1050 20 1200 30 L1200 110 L0 110Z" fill="var(--green)"/>
    <path d="M0 66 C250 34 450 104 720 86 C900 74 1050 36 1200 44 L1200 110 L0 110Z" fill="#fff"/>
  </svg>
</section>

<section class="welcome">
  <h2 class="section-title" style="top:846px">Welcome To Stride Leaf</h2>
  <p class="lead" style="top:926px">Lorem ipsum dolor sit amet, consectetur adipiscing elit, sed do eiusmod tempor incididunt ut labore et dolore magna aliqua. Ut enim ad minim veniam, quis nostrud exercitation ullamco laboris nisi ut aliquip.</p>
  <div class="abs" style="left:115px;top:995px;width:80px;height:80px;border-radius:50%;background:#e6f4df"></div>
  <div class="step-number">02</div>
  <div class="dots" style="left:198px;width:236px"></div>
  <div class="dots" style="left:765px;width:233px"></div>
  <div class="funnel-bar bar-dark" style="left:401px;top:1056px;width:398px">Increases Energy &amp; Reduces Stress</div>
  <div class="funnel-bar bar-green" style="left:429px;top:1143px;width:340px">Relieves Muscle &amp; Joint Pain</div>
  <div class="funnel-bar bar-dark" style="left:461px;top:1228px;width:276px">Promote Weight Loss</div>
  <div class="abs" role="img" aria-label="Person touching a sore shoulder" style="left:1003px;top:1130px;width:88px;height:88px;border-radius:50%;background:#eef0ee"></div>
  <div class="abs" role="img" aria-label="White insole with brand print" style="left:447px;top:1328px;width:336px;height:95px;border-radius:48px;background:linear-gradient(180deg,#f6f6f6,#e2e2e2)"></div>
</section>

<section class="why">
  <svg class="abs" style="left:0;top:-40px" width="1200" height="80" viewBox="0 0 1200 80"><path d="M0 40 C300 80 800 0 1200 30 L1200 80 L0 80Z" fill="var(--light)"/></svg>
  <h2 class="section-title" style="top:140px">Why Choose Us?</h2>
  <div class="why-circle" style="left:132px;top:300px;width:250px;height:250px">
    <svg width="70" height="66" viewBox="0 0 70 66"><path d="M35 28C20 16 22 4 31 5c2 0 4 2 4 4 0-2 2-4 4-4 9-1 11 11-4 23z" fill="var(--green)"/><path d="M5 30l14 18 16 6M65 30L51 48l-16 6" fill="none" stroke="var(--green)" stroke-width="4"/></svg>
    <h3>A Totally Natural<br>Solution Without Any<br>Health Risk</h3>
  </div>
  <div class="why-circle why-main" style="left:432px;top:262px;width:334px;height:334px">
    <svg width="80" height="64" viewBox="0 0 80 64"><circle cx="32" cy="14" r="10" fill="#fff"/><path d="M14 60c0-16 8-26 18-26s18 10 18 26z" fill="#fff"/><circle cx="56" cy="44" r="14" fill="var(--green)" stroke="#fff" stroke-width="4"/><path d="M49 44l5 5 9-9" fill="none" stroke="#fff" stroke-width="4"/></svg>
    <h3>Approved By Acupressure Expert</h3>
    <p>Lorem ipsum dolor consectetur adipiscing elit eiusmod tempor incidi dunt ut labore et dolore</p>
    <svg width="24" height="24" style="margin-top:10px"><circle cx="12" cy="12" r="11" fill="#fff"/><path d="M7 10l5 5 5-5" fill="none" stroke="var(--green)" stroke-width="2.5"/></svg>
  </div>
  <div class="why-circle" style="left:814px;top:300px;width:250px;height:250px">
    <svg width="70" height="70" viewBox="0 0 70 70" fill="none" stroke="var(--green)" stroke-width="3"><circle cx="35" cy="33" r="16"/><path d="M29 52h12M30 58h10M35 3v7M10 12l5 5M60 12l-5 5M3 33h7M60 33h7M37 23l-6 11h8l-6 11"/></svg>
    <h3>A Unique Design<br>Based On Two Types Of<br>Knowledge</h3>
  </div>
</section>

<section class="features">
  <h2 class="section-title" style="top:2348px">Our Features</h2>
  <p class="lead" style="top:2421px">Lorem ipsum dolor sit amet, consectetur adipiscing elit, sed do eiusmod tempor incididunt ut labore et dolore magna aliqua. Ut enim ad minim veniam, quis nostrud exercitation ullamco laboris nisi ut aliquip.</p>
  <div class="feature-photo" role="img" aria-label="Bare foot stepping onto a dark insole"></div>
  <div class="feature" style="top:2524px"><svg width="80" height="74" viewBox="0 0 80 74" fill="none" stroke="#333" stroke-width="2.5"><path d="M22 4c4 20 6 30 2 44l-4 22M58 4c-4 20-6 30-2 44l4 22M26 46h28M30 60c6 6 14 6 20 0"/><path d="M4 22l10 0M9 17l5 5-5 5M76 22H66M71 17l-5 5 5 5" stroke="var(--green)"/></svg><h4>Lose Weight</h4><p>Lorem ipsum dolor sit amet consectetur adipiscing elit sed do eiusmod tempor incididunt ut labore.</p></div>
  <div class="feature" style="top:2633px"><svg width="80" height="74" viewBox="0 0 80 74" fill="none" stroke="#333" stroke-width="2.5"><path d="M22 10C12 26 8 34 8 42a14 14 0 0 0 28 0c0-8-4-16-14-32z"/><path d="M52 22C40 40 36 48 36 56a16 16 0 0 0 32 0c0-8-4-16-16-34z"/></svg><h4>Blood Flow</h4><p>Lorem ipsum dolor sit amet consectetur adipiscing elit sed do eiusmod tempor incididunt ut labore.</p></div>
  <div class="feature" style="top:2742px"><svg width="80" height="74" viewBox="0 0 80 74" fill="none" stroke="#333" stroke-width="2.5"><path d="M40 6h30M40 6c-8 10-10 22-6 32l4 30M34 38c-6 4-10 14-10 30"/><path d="M6 20l12 6M4 34h14M10 48l10-6" stroke="var(--green)"/></svg><h4>Joint Pain</h4><p>Lorem ipsum dolor sit amet consectetur adipiscing elit sed do eiusmod tempor incididunt ut labore.</p></div>
  <div class="feature" style="top:2849px"><svg width="80" height="74" viewBox="0 0 80 74" fill="none" stroke="var(--green)" stroke-width="2.5"><circle cx="40" cy="14" r="9"/><path d="M40 23v22M40 30l-16 14M40 30l16 14M18 64c8-10 36-10 44 0M14 70h52"/></svg><h4>Reduces Stress</h4><p>Lorem ipsum dolor sit amet consectetur adipiscing elit sed do eiusmod tempor incididunt ut labore.</p></div>
</section>

<section class="benefits">
  <svg class="abs" style="left:0;top:0" width="1200" height="617" viewBox="0 0 1200 617"><polygon points="158,0 1044,0 585,617" fill="var(--green)"/></svg>
  <h2 class="section-title" style="top:86px;color:#fff">Our Benefits</h2>
  <div class="benefit-card" style="left:113px">
    <svg width="70" height="70" viewBox="0 0 70 70" fill="none" stroke="var(--green)" stroke-width="3"><circle cx="35" cy="35" r="31"/><path d="M50 20L20 50M50 20l-6 16M50 20l-16 6"/></svg>
    <h4>Powerful Magnet</h4><p>Lorem ipsum dolor sit amet, consectetur adipiscing elit seo eiusmod tempor</p>
  </div>
  <div class="benefit-card" style="left:360px">
    <svg width="90" height="70" viewBox="0 0 90 70" fill="none" stroke="var(--green)" stroke-width="3"><path d="M6 52c0-18 6-30 14-36 8 10 20 14 32 14 18 0 32 8 32 18v6H6zM6 60h78M28 24l8-4M34 30l8-4"/></svg>
    <h4>For All Type Of Shoes</h4><p>Just for the health of it! Our Health Walk is fun for the whole family! It will be held</p>
  </div>
  <div class="benefit-card" style="left:609px">
    <svg width="70" height="70" viewBox="0 0 70 70" fill="none" stroke="var(--green)" stroke-width="3"><path d="M35 22l18 10-18 10-18-10zM17 42l18 10 18-10M35 6v10M6 6l10 10M64 6L54 16M35 56v10M30 61l5 5 5-5"/></svg>
    <h4>Flexible And Light</h4><p>Lorem ipsum dolor sit amet, consectetur adipiscing elit seo eiusmod tempor</p>
  </div>
  <div class="benefit-card" style="left:856px">
    <svg width="70" height="70" viewBox="0 0 70 70" fill="none" stroke="var(--green)" stroke-width="3"><path d="M18 30c-6-8 6-12 0-22M35 30c-6-8 6-12 0-22M52 30c-6-8 6-12 0-22M14 8l4-4 4 4M31 8l4-4 4 4M48 8l4-4 4 4M8 40h54M8 48h54M18 66c-6-8 6-8 0-14M35 66c-6-8 6-8 0-14M52 66c-6-8 6-8 0-14"/></svg>
    <h4>Breathable</h4><p>Lorem ipsum dolor sit amet, consectetur adipiscing elit seo eiusmod tempor</p>
  </div>
</section>

<section class="products">
  <div class="product" style="left:111px"><div class="product-photo" role="img" aria-label="Feet on tiptoe beside a colourful pair of insoles" style="background:linear-gradient(135deg,#f2ece8,#e3c4b3 45%,#2346a8 70%,#f0c420)"></div><div class="product-label" style="background:var(--dark)">FOR MEN AND WOMEN</div></div>
  <div class="product" style="left:451px"><div class="product-photo" role="img" aria-label="Gloved hands fitting an insole to a foot" style="background:linear-gradient(135deg,#f4f4f4,#e4c6b2 45%,#4a70d0 70%,#2a2a2a)"></div><div class="product-label" style="background:var(--green)">ONE SIZE FOR ALL</div></div>
  <div class="product" style="left:789px"><div class="product-photo" role="img" aria-label="Foot pressed into a moulding foam tray" style="background:linear-gradient(135deg,#8a9aa6,#d8a494 45%,#2c4fd0 65%,#c47f6e)"></div><div class="product-label" style="background:var(--dark)">ADJUSTABLE BY CUTTING</div></div>
</section>

<section class="services">
  <h2 class="service-title">WHAT WE DO FOR YOU</h2>
  <p class="lead" style="top:170px;left:330px;width:540px;line-height:24px">All new account applicants must provide all the following documentations to be eligible for an account at StrideLeaf.</p>
  <svg class="chev" style="left:48px" width="14" height="24"><path d="M12 2L2 12l10 10" fill="none" stroke="#999" stroke-width="2"/></svg>
  <svg class="chev" style="left:1134px" width="14" height="24"><path d="M2 2l10 10-10 10" fill="none" stroke="#999" stroke-width="2"/></svg>
  <div class="service-card" style="left:99px"><div class="service-icon"><svg width="36" height="26" viewBox="0 0 36 26" fill="none" stroke="var(--green)" stroke-width="2.5"><path d="M2 4h20v14H2zM22 9h7l5 5v4h-12"/><circle cx="8" cy="21" r="3"/><circle cx="28" cy="21" r="3"/></svg></div><h4>FREE SHIPPING</h4><p>Nemo enim ipsam vollg hluptatem quia voluptas sit aut odit</p></div>
  <div class="service-card" style="left:360px"><div class="service-icon"><svg width="32" height="32" viewBox="0 0 32 32" fill="none" stroke="var(--green)" stroke-width="2.5"><circle cx="16" cy="12" r="7"/><path d="M6 30c0-8 4-11 10-11s10 3 10 11M7 12a9 9 0 0 1 18 0"/></svg></div><h4>CUSTOMER SERVICE</h4><p>Nemo enim ipsam vollg hluptatem quia voluptas sit aut odit</p></div>
  <div class="service-card" style="left:619px"><div class="service-icon"><svg width="32" height="32" viewBox="0 0 32 32" fill="none" stroke="var(--green)" stroke-width="2.5"><circle cx="16" cy="14" r="10"/><path d="M16 8v12M12 11h6a2 2 0 0 1 0 4h-4a2 2 0 0 0 0 4h6M8 30l8-6 8 6"/></svg></div><h4>MONEY BACK GUARANTEE</h4><p>Nemo enim ipsam vollg hluptatem quia voluptas sit aut odit</p></div>
  <div class="service-card" style="left:878px"><div class="service-icon"><svg width="34" height="28" viewBox="0 0 34 28" fill="none" stroke="var(--green)" stroke-width="2.5"><rect x="2" y="8" width="26" height="17" rx="2"/><path d="M2 14h26M8 4h24v16"/></svg></div><h4>SAFE PAYMENT</h4><p>Nemo enim ipsam vollg hluptatem quia voluptas sit aut odit</p></div>
</section>

<footer class="site-footer">
  <div class="footer-col" style="left:109px"><h4>QUICK LINKS</h4><ul><li>Home</li><li>About Us</li><li>Products</li><li>Shop</li><li>Reviews</li><li>Contact us</li></ul></div>
  <div class="footer-col" style="left:354px"><h4>ACCOUNT</h4><ul><li>Payment</li><li>Save cards</li><li>Shipping</li><li>Return</li><li>FAQ</li><li>Check Out</li></ul></div>
  <div class="footer-col" style="left:575px;width:270px"><h4>CONTACT US</h4>
    <div class="contact-row"><svg width="14" height="18" viewBox="0 0 14 18"><path d="M7 17S1 10 1 6.5a6 6 0 0 1 12 0C13 10 7 17 7 17z" fill="none" stroke="#ddd" stroke-width="1.5"/><circle cx="7" cy="6.5" r="2" fill="#ddd"/></svg><span>48 Meadow Lane, Greenbrook,<br>Vale County</span></div>
    <div class="contact-row"><svg width="14" height="14" viewBox="0 0 14 14"><path d="M2 1h3l1.5 3.5-2 1.5a8 8 0 0 0 3.5 3.5l1.5-2L13 9v3a1 1 0 0 1-1 1A11 11 0 0 1 1 2a1 1 0 0 1 1-1z" fill="none" stroke="#ddd" stroke-width="1.3"/></svg><span>(+1) 555 014 2290</span></div>
    <div class="contact-row"><svg width="14" height="12" viewBox="0 0 14 12"><rect x="1" y="1" width="12" height="10" fill="none" stroke="#ddd" stroke-width="1.3"/><path d="M1 1l6 5 6-5" fill="none" stroke="#ddd" stroke-width="1.3"/></svg><span>contact@strideleaf.example</span></div>
  </div>
  <div class="footer-col" style="left:872px"><h4>SOCIAL MEDIA</h4>
    <div class="social"><span></span><span></span><span></span><span></span><span></span></div>
    <h4 style="margin:28px 0 0">MAKE PAYMENT</h4>
    <div class="pay"><span></span><span></span><span></span><span></span></div>
  </div>
  <div class="footer-rule"></div>
  <a class="to-top"><svg width="22" height="22" viewBox="0 0 22 22"><path d="M4 12l7-7 7 7M4 19l7-7 7 7" fill="none" stroke="#fff" stroke-width="2.5"/></svg></a>
  <p class="copyright">© Copyright 2019 StrideLeaf. All Rights Reserved</p>
</footer>

</body>
</html>
```